Poster

I need a poster for my business, www.coastalsupperroutesnerja.example which some information about the most important activities (Sangria Tasting, Iberian Ham, Charcuteries & Sherry Wine Tasting, Sailboat Experiences and Picnic Experiences). A3 Format. Social media included (@coastalsupperroutescsr), contact information included.

```html
<!DOCTYPE html>
<html lang="en">
<head>
<meta charset="utf-8">
<title>Coastal Supper Routes – Poster</title>
<link rel="stylesheet" href="https://fonts.googleapis.com/css2?family=Montserrat:wght@600;700;800;900&family=Playball&display=swap">
<style>
  :root {
    --sky-top: #7f6c9e;
    --sky-mid: #c98aa0;
    --horizon: #f2a27a;
    --sea-light: #8a6f86;
    --sea-deep: #2e2238;
    --band-start: #9b4fa6;
    --band-end: #5a4a9c;
    --ink: #111018;
    --white: #ffffff;
  }
  * { box-sizing: border-box; margin: 0; padding: 0; }
  html, body { width: 849px; height: 1200px; overflow: hidden; background: var(--sea-deep); }
  .poster {
    position: relative;
    width: 849px;
    height: 1200px;
    overflow: hidden;
    font-family: "Montserrat", sans-serif;
    color: var(--white);
  }
  .backdrop {
    position: absolute; inset: 0;
    background: linear-gradient(180deg,
      var(--sky-top) 0%,
      #9a7aa6 12%,
      var(--sky-mid) 24%,
      #e7978c 31%,
      var(--horizon) 36%,
      #d48a86 42%,
      var(--sea-light) 52%,
      #5c4462 66%,
      #3f2f4a 80%,
      var(--sea-deep) 100%);
  }
  .outlined {
    -webkit-text-stroke: 2px var(--ink);
    paint-order: stroke fill;
    text-shadow: 2px 3px 0 var(--ink);
  }
  .headline { position: absolute; left: 0; right: 0; top: 138px; text-align: center; }
  .eyebrow {
    font-weight: 600; font-size: 38px; letter-spacing: 1px;
    display: flex; justify-content: center; align-items: center; gap: 10px;
  }
  .eyebrow .dash { display: inline-block; width: 40px; height: 5px; background: var(--white); border: 1.5px solid var(--ink); box-shadow: 2px 2px 0 var(--ink); }
  .title-script {
    font-family: "Playball", cursive;
    font-weight: 400;
    font-size: 86px; line-height: 1; margin-top: 14px;
    -webkit-text-stroke: 4px var(--ink);
    paint-order: stroke fill;
    text-shadow: 3px 4px 0 var(--ink);
  }
  .subtitle { font-weight: 600; font-size: 37px; margin-top: 20px; letter-spacing: 0.3px; }

  .experiences {
    position: absolute; left: 43px; top: 418px;
    display: grid; grid-template-columns: 353px 353px; column-gap: 57px; row-gap: 36px;
  }
  .experience-card {
    width: 353px; height: 238px; border-radius: 26px; overflow: hidden;
    position: relative;
    box-shadow: 0 0 18px 6px rgba(255,255,255,0.45);
  }
  .experience-photo { position: absolute; left: 0; right: 0; top: 0; height: 186px; }
  .photo-sangria { background: linear-gradient(160deg, #e9eef3 0%, #d7dde6 45%, #7a4fa1 75%, #5a3b80 100%); }
  .photo-tasting { background: linear-gradient(135deg, #6e6a62 0%, #3a3530 45%, #1f1c1a 70%, #2f6a5c 100%); }
  .photo-sailboat { background: linear-gradient(180deg, #e8e0cf 0%, #b8c2c4 40%, #4a7e95 65%, #1f4d66 100%); }
  .photo-picnic { background: linear-gradient(170deg, #8aa3b3 0%, #b59a7f 40%, #8b5a33 65%, #e5ddd2 100%); }
  .experience-label {
    position: absolute; left: 0; right: 0; bottom: 0; height: 54px;
    background: linear-gradient(90deg, var(--band-start), var(--band-end));
    display: flex; align-items: center; justify-content: center; text-align: center;
    font-weight: 800; font-size: 17px; letter-spacing: 1.2px; line-height: 1.2;
    text-transform: uppercase; padding-top: 6px;
  }
  .label-wave { position: absolute; left: 0; top: 0; width: 353px; height: 8px; }

  .contact { position: absolute; left: 0; right: 0; top: 990px; text-align: center; }
  .contact-title { font-weight: 900; font-size: 51px; line-height: 1; -webkit-text-stroke: 3px var(--ink); }
  .contact-handle { font-weight: 800; font-size: 36px; line-height: 1; margin-top: 24px; }
  .contact-site { font-weight: 800; font-size: 33px; line-height: 1; margin-top: 22px; }
</style>
</head>
<body>
<main class="poster">
  <div class="backdrop" role="img" aria-label="Sunset sky over the sea, purple and orange tones"></div>

  <header class="headline">
    <p class="eyebrow outlined"><span class="dash"></span>ENJOY<span class="dash"></span></p>
    <h1 class="title-script">Marbella &amp; Estepona</h1>
    <p class="subtitle outlined">WITH COASTAL SUPPER ROUTES</p>
  </header>

  <section class="experiences">
    <article class="experience-card">
      <div class="experience-photo photo-sangria" role="img" aria-label="Glasses of sangria and cheese on a terrace table"></div>
      <div class="experience-label">
        <svg class="label-wave" viewBox="0 0 353 8" preserveAspectRatio="none"><path d="M0 3 Q5.5 8 11 3 T22 3 T33 3 T44 3 T55 3 T66 3 T77 3 T88 3 T99 3 T110 3 T121 3 T132 3 T143 3 T154 3 T165 3 T176 3 T187 3 T198 3 T209 3 T220 3 T231 3 T242 3 T253 3 T264 3 T275 3 T286 3 T297 3 T308 3 T319 3 T330 3 T341 3 T352 3" fill="none" stroke="#fff" stroke-width="2"/></svg>
        Sangria Tasting
      </div>
    </article>
    <article class="experience-card">
      <div class="experience-photo photo-tasting" role="img" aria-label="Bowl of olives and cured ham slices on a green board"></div>
      <div class="experience-label">
        <svg class="label-wave" viewBox="0 0 353 8" preserveAspectRatio="none"><path d="M0 3 Q5.5 8 11 3 T22 3 T33 3 T44 3 T55 3 T66 3 T77 3 T88 3 T99 3 T110 3 T121 3 T132 3 T143 3 T154 3 T165 3 T176 3 T187 3 T198 3 T209 3 T220 3 T231 3 T242 3 T253 3 T264 3 T275 3 T286 3 T297 3 T308 3 T319 3 T330 3 T341 3 T352 3" fill="none" stroke="#fff" stroke-width="2"/></svg>
        Iberian Ham, Charcuteries<br>&amp; Sherry Wine Tasting
      </div>
    </article>
    <article class="experience-card">
      <div class="experience-photo photo-sailboat" role="img" aria-label="Sailboat on the open sea at sunset"></div>
      <div class="experience-label">
        <svg class="label-wave" viewBox="0 0 353 8" preserveAspectRatio="none"><path d="M0 3 Q5.5 8 11 3 T22 3 T33 3 T44 3 T55 3 T66 3 T77 3 T88 3 T99 3 T110 3 T121 3 T132 3 T143 3 T154 3 T165 3 T176 3 T187 3 T198 3 T209 3 T220 3 T231 3 T242 3 T253 3 T264 3 T275 3 T286 3 T297 3 T308 3 T319 3 T330 3 T341 3 T352 3" fill="none" stroke="#fff" stroke-width="2"/></svg>
        Sailboat Experiences
      </div>
    </article>
    <article class="experience-card">
      <div class="experience-photo photo-picnic" role="img" aria-label="Picnic basket with bread, wine, cheese and grapes by the sea"></div>
      <div class="experience-label">
        <svg class="label-wave" viewBox="0 0 353 8" preserveAspectRatio="none"><path d="M0 3 Q5.5 8 11 3 T22 3 T33 3 T44 3 T55 3 T66 3 T77 3 T88 3 T99 3 T110 3 T121 3 T132 3 T143 3 T154 3 T165 3 T176 3 T187 3 T198 3 T209 3 T220 3 T231 3 T242 3 T253 3 T264 3 T275 3 T286 3 T297 3 T308 3 T319 3 T330 3 T341 3 T352 3" fill="none" stroke="#fff" stroke-width="2"/></svg>
        Picnic Experiences
      </div>
    </article>
  </section>

  <footer class="contact">
    <p class="contact-title outlined">CONTACT US!</p>
    <p class="contact-handle outlined">@coastalsupperroutescsr</p>
    <p class="contact-site outlined">www.coastalsupperroutesnerja.example</p>
  </footer>
</main>
</body>
</html>
```